tinyTally Resource Book - 10 maths tasks to do outside

I need a 22 (11 pages back to back) page A6 sized book produced to standard for submission to professional printer. Needs to be as .pdf file showing guide lines and allowances for colour bleed. I have text already written and submitted as attachment in a Word file with margins set to A6 size. The theme of the materials is "Nature Play" so using lots of pictures from nature (Australia preferably) and showing lots of patterns in nature (rocks, leaves, flower petals etc). Some of the tasks refer to specific activities, such as "shadows" and "floating" so would be great to illustrate appropriately. The big emphasis is on learning outside the classroom, getting kids to engage actively with nature. I would like to see the pages as full colour - so not white background. The book itself will be spiral bound along the top edge so a margin of at least 1cm will be required at the top of each page (or the bottom of even numbered pages). Book will be printed on plastic laminated matte paper for outdoor use. Font size needs to be big enough to read. Fonts sizes, alignments and page numbers are all different at the moment and need to be standardised. One photo is included in a page as a sample if you can use it, otherwise disregard. Logo for Wattlebrook Numeracy Guild is also included to have as part of the acknowledgements at the back of the book.

Target Market(s)

Book is for early childhood and preschool teachers.

Industry/Entity Type

Education

Font styles to use
Sans Serif

Requirements
Must have
• Colour and appeal.
Nice to have
• Use of natural colours instead of bright catchy colours but that is your call.
Should not have
• American spelling

```html
<!DOCTYPE html>
<html lang="en-AU">
<head>
<meta charset="utf-8">
<title>tinyTally – Big Bigger Biggest</title>
<link rel="stylesheet" href="https://fonts.googleapis.com/css2?family=Fredoka:wght@700&family=Open+Sans:wght@500&display=swap">
<style>
  :root {
    --heading-blue: #2b3490;
    --heading-edge: #ffffff;
    --bullet-red: #d7202b;
    --body-ink: #161616;
    --sea-deep: #6d8fc2;
    --sea-light: #a9c0dd;
    --shore: #d7c6ad;
    --sand: #cfb898;
    --sand-deep: #c3a987;
  }
  * { margin: 0; padding: 0; box-sizing: border-box; }
  html, body { width: 848px; height: 1200px; overflow: hidden; }
  body { position: relative; font-family: "Open Sans", sans-serif; }

  .page-backdrop {
    position: absolute; inset: 0;
    background: linear-gradient(180deg,
      var(--sea-deep) 0%, var(--sea-light) 30%, #c9cfd3 38%,
      var(--shore) 42%, var(--sand) 65%, var(--sand-deep) 100%);
  }

  .task-section { position: absolute; left: 55px; right: 20px; }
  .section-heading {
    font-family: "Fredoka", sans-serif;
    font-weight: 700;
    font-size: 56px;
    line-height: 1;
    color: var(--heading-blue);
    -webkit-text-stroke: 6px var(--heading-edge);
    paint-order: stroke fill;
    letter-spacing: 0.5px;
  }
  .bullet-list { list-style: none; margin-left: 108px; margin-top: 6px; }
  .bullet-list li {
    position: relative;
    font-size: 30px;
    line-height: 41.5px;
    color: var(--body-ink);
  }
  .bullet-list li::before {
    content: "";
    position: absolute;
    left: -40px; top: 12px;
    width: 17px; height: 17px;
    background: var(--bullet-red);
    transform: rotate(45deg);
  }

  .task-steps { top: 78px; }
  .prompting { top: 366px; }
  .variations { top: 610px; }
  .big-ideas { top: 766px; }
</style>
</head>
<body>
  <div class="page-backdrop" role="img" aria-label="Photograph of a sandy beach with blue sea behind and a stack of three smooth white stones"></div>

  <section class="task-section task-steps">
    <h1 class="section-heading">2. Big Bigger Biggest</h1>
    <ul class="bullet-list">
      <li>Find an object – stone, leaf, stick etc</li>
      <li>Now find a bigger one</li>
      <li>Now find an even bigger one than that</li>
      <li>Line them up – big bigger biggest</li>
      <li>Keep adding to your line</li>
    </ul>
  </section>

  <section class="task-section prompting">
    <h2 class="section-heading">Prompting questions</h2>
    <ul class="bullet-list">
      <li>Where do you put new rocks in the<br>line?</li>
      <li>Can you take away some rocks to make<br>your “biggest” the “smallest”?</li>
    </ul>
  </section>

  <section class="task-section variations">
    <h2 class="section-heading">Variations</h2>
    <ul class="bullet-list">
      <li>Small Smaller Smallest</li>
      <li>Long Longer Longest</li>
    </ul>
  </section>

  <section class="task-section big-ideas">
    <h2 class="section-heading">Big Ideas</h2>
    <ul class="bullet-list">
      <li>Comparison</li>
      <li>Visualization</li>
      <li>Prediction</li>
    </ul>
  </section>
</body>
</html>
```